High-end Oceanfront Real Estate Group Needs Clean, Modern Web Design

I’m looking for a clean, professional, modern and beautiful homepage web design for a Real Estate group in Southern California, USA.

The group/company is “Marwick on the Shore,” and they specialize in high end (i.e. expensive), oceanfront real estate in the Orange County area.

The look and feel of the page should accentuate the brand qualities: luxurious/expensive, professional, and beautiful (Orange County is one of the most beautiful areas in all the US and we would love the site to emphasize the beautiful beaches and scenery it has to offer).

Looks we like:
• www.brantleyhomesrealty.example
• www.closedbyvane.example -- I think the design is pretty out-dated in this site, but I like the organization/layout of the site

Header Tags (I don’t know if we can fit all of these, may need a side-menu, but I’d prefer header title only if possible):
• Welcome
• Featured Listings
• Previously Sold
• Sell
• Property Search
• Team
• Videos
• Blog
• Explore O.C.
• Contact

I have attached the beach and logo pics that we would like to use as the header, a few pictures of the team, and one sample home/view pic which can be used in any of the other sections (for pictures of the homes, just find expensive oceanfront houses and that will be fine).

I promise to provide feedback to each and every design submission. I appreciate the hard work that all of you are putting into your designs. There can be only one contest winner, but I hope to give all of you helpful feedback to submit the best designs possible!

Target Market(s)

Very wealthy home owners of oceanfront properties. These properties are worth several millions of dollars, and thus the site and brand needs to be targeted to very wealthy, successful individuals and families (both US and international buyers).

Industry/Entity Type

Real Estate

Number of Pages Required

2 page

Requirements
Must have
• I don’t want to give too many requirements, because I want to let you all be creative. However, here are the few Must Haves:
• Must submit 2 page designs (a home page and a sub page)
• Must use logo provided
• Focus is mostly on homes, but I would like to include some beach/ocean imagery as well
• The first “item” on the home page should be an accordion/slider which shows pictures of homes and with 1 line of text: “List with the Leader” and two link buttons: “Sell Your Home” and “Buy Your Home”
• Color palette needs to be mainly blues--to match ocean and sky blue
• Exported in all major formats (psd,ai,eps,png,jpeg,etc)
Nice to have
• We don’t necessarily need all of these, but would like to feature most:
• List of videos
• “Meet the Team”—brief team bios and pics
• Link(s) to Blog
• “List with the Leader” – section on why they should choose this firm
• Featured Listings
• Previously Sold

```html
<!DOCTYPE html>
<html lang="en">
<head>
<meta charset="utf-8">
<title>Marwick on the Shore — Oceanfront Real Estate</title>
<link href="https://fonts.googleapis.com/css2?family=Roboto:wght@300;400;500;700&family=Roboto+Condensed:wght@400;700&display=swap" rel="stylesheet">
<style>
:root{
  --blue:#1b8fd8;
  --blue-dark:#136aa6;
  --navy:#0d1f30;
  --navy-2:#14304a;
  --ink:#222;
  --muted:#666;
  --light:#f1f3f5;
  --white:#fff;
}
*{box-sizing:border-box;margin:0;padding:0}
html,body{width:1200px;height:3428px;overflow:hidden}
body{font-family:"Roboto",Arial,sans-serif;color:var(--ink);background:var(--white);position:relative}
.cond{font-family:"Roboto Condensed","Roboto",Arial,sans-serif}

/* Header */
.site-header{height:150px;position:relative;background:linear-gradient(180deg,#e9f1f8,#d6e4ef)}
.brand{position:absolute;left:38px;top:22px;display:flex;align-items:center;gap:14px}
.brand-mark{width:22px;height:22px;background:var(--blue)}
.brand-name{font-family:"Roboto Condensed",sans-serif;font-size:44px;font-weight:400;color:var(--navy-2);letter-spacing:1px;line-height:1}
.contact-top{position:absolute;right:40px;top:38px;text-align:right}
.contact-top .phone{display:flex;align-items:center;gap:10px;font-size:34px;font-weight:700;color:var(--navy-2)}
.contact-top .addr{font-size:13px;color:#555;margin-top:8px}

/* Nav */
.main-nav{height:50px;background:var(--navy);display:flex;padding-left:40px}
.main-nav a{display:flex;align-items:center;padding:0 17px;color:#dfe7ee;font-size:14px;font-weight:500;text-decoration:none;text-transform:uppercase}
.main-nav a.active{background:var(--blue);color:#fff}

/* Hero */
.hero{height:600px;position:relative;background:linear-gradient(180deg,#3d7fbf 0%,#8ab6d9 38%,#c9c2b1 60%,#5d6b52 82%,#2f5d7a 100%)}
.hero-box{position:absolute;left:132px;top:226px;width:460px;height:182px;background:rgba(10,22,34,.55);padding:30px 32px}
.hero-box h1{font-family:"Roboto Condensed",sans-serif;font-size:44px;font-weight:700;color:#fff}
.hero-btns{display:flex;gap:12px;margin-top:26px}
.btn{display:inline-block;padding:14px 24px;font-size:15px;font-weight:500;color:#fff;text-transform:uppercase}
.btn-blue{background:var(--blue)}
.btn-dark{background:rgba(15,30,45,.9)}
.hero-arrow{position:absolute;top:300px;width:26px;height:44px}
.hero-arrow.l{left:24px}.hero-arrow.r{right:24px}

/* Section titles */
.sec-title{text-align:center;font-family:"Roboto Condensed",sans-serif;font-size:36px;font-weight:700;text-transform:uppercase}
.sec-title .hl{color:var(--blue)}
.sec-sub{text-align:center;font-size:16px;color:#444;margin-top:14px}

/* Videos */
.videos{height:560px;padding-top:160px}
.video-row{display:flex;justify-content:center;gap:28px;margin-top:52px}
.video-card{width:398px;background:#fff;border:1px solid #ccc;padding:8px;box-shadow:0 2px 6px rgba(0,0,0,.15)}
.video-still{height:170px;position:relative;display:flex;align-items:center;justify-content:center}
.video-still.a{background:linear-gradient(180deg,#6fa4c9,#b99c79 55%,#3a6f8e)}
.video-still.b{background:linear-gradient(180deg,#8a6440,#c49a6a 50%,#6a4a2f)}
.video-bar{height:24px;background:#1e1e1e;display:flex;align-items:center;padding:0 10px;gap:10px}
.video-bar .track{flex:1;height:4px;background:#555}
.video-bar .track i{display:block;width:30%;height:100%;background:var(--blue)}
.video-bar span{font-size:10px;color:#bbb}

/* Dark bands */
.band{background:linear-gradient(180deg,#10263b,#1f3e58 50%,#112538);color:#fff}
.band .sec-title{color:#fff}
.featured{height:400px;padding-top:40px}
.listing-row{display:flex;justify-content:center;gap:12px;margin-top:34px}
.listing{width:238px}
.listing .thumb{height:152px;border:3px solid #fff}
.listing h4{font-size:13px;font-weight:700;margin-top:10px;text-transform:uppercase}
.listing p{font-size:11px;color:#c9d3dc;margin-top:5px;line-height:1.4}
.listing .more{font-size:11px;color:#fff;margin-top:5px;display:block}

/* Leader */
.leader{height:320px;background:linear-gradient(90deg,#dfe6ec,#eef1f3 40%,#e5e8ea);position:relative}
.leader-photo{position:absolute;left:88px;top:70px;width:148px;height:148px;border-radius:50%;border:5px solid #fff;background:linear-gradient(180deg,#c9b7a4,#6e5a4b);box-shadow:0 2px 6px rgba(0,0,0,.25)}
.leader-text{position:absolute;left:312px;top:70px;width:812px}
.leader-text h2{font-family:"Roboto Condensed",sans-serif;font-size:28px;font-weight:700;text-transform:uppercase}
.leader-text h2 .hl{color:var(--blue)}
.leader-text p{font-size:15px;line-height:1.55;color:#333;margin-top:10px}
.btn-read{display:inline-block;background:var(--navy-2);color:#fff;font-size:13px;padding:9px 18px;margin-top:14px;border-radius:3px}

/* Team */
.team{height:470px;padding-top:80px}
.team-row{display:flex;justify-content:center;gap:20px;margin-top:36px}
.member{width:192px;height:200px;position:relative}
.member.m1{background:linear-gradient(180deg,#8a8f95,#4b4f55)}
.member.m2{background:linear-gradient(180deg,#d8d8d8,#5c5c5c)}
.member.m3{background:linear-gradient(180deg,#bfc6cf,#8c7b6b)}
.member.m4{background:linear-gradient(180deg,#f2f2f2,#7a7a7a)}
.member .name{position:absolute;left:0;right:0;bottom:52px;text-align:center;font-size:12px;font-weight:700;color:#fff;text-transform:uppercase}

/* Sold */
.sold{height:460px;padding-top:48px}
.sold-row{display:flex;justify-content:center;gap:26px;margin-top:34px}
.sold .listing{width:324px}
.sold .listing .thumb{height:196px}

/* Footer */
.site-footer{height:260px;background:#eceef0;display:flex;padding:38px 0 0 78px;gap:0}
.fcol{width:380px}
.fcol h5{font-size:13px;color:var(--blue);text-transform:uppercase;font-weight:500;margin-bottom:12px}
.fcol p,.fcol li{font-size:12px;color:#555;line-height:1.6}
.fcol ul{list-style:none}
.fcol li{display:flex;align-items:center;gap:8px;margin-bottom:6px}
.fcol li::before{content:"";width:5px;height:5px;background:var(--blue);border-radius:50%}
.footer-bar{height:148px;background:var(--navy);color:#c8d1d9;padding:34px 78px;position:relative}
.footer-bar .links{font-size:13px}
.footer-bar .copy{font-size:12px;margin-top:10px;color:#8e9aa5}
.socials{position:absolute;right:78px;top:34px;display:flex;gap:8px}
.socials i{width:24px;height:24px;background:var(--blue);display:block}
.to-top{position:absolute;right:20px;bottom:18px;width:22px;height:22px;background:#2a3c4d}
</style>
</head>
<body>

<header class="site-header">
  <div class="brand">
    <span class="brand-mark"></span>
    <span class="brand-name">Marwick on the Shore</span>
  </div>
  <div class="contact-top">
    <div class="phone">
      <svg width="30" height="30" viewBox="0 0 24 24"><path fill="#14304a" d="M6.6 10.8a15 15 0 0 0 6.6 6.6l2.2-2.2a1 1 0 0 1 1-.25 11.4 11.4 0 0 0 3.6.57 1 1 0 0 1 1 1V20a1 1 0 0 1-1 1A17 17 0 0 1 3 4a1 1 0 0 1 1-1h3.5a1 1 0 0 1 1 1c0 1.25.2 2.45.57 3.6a1 1 0 0 1-.25 1z"/></svg>
      949.555.0142
    </div>
    <div class="addr">1480 Coastline Drive, Laguna Beach, CA</div>
  </div>
</header>

<nav class="main-nav">
  <a class="active">Welcome</a><a>Featured Listings</a><a>Previously Sold</a><a>Sell</a><a>Property Search</a><a>Team</a><a>Videos</a><a>Blog</a><a>Explore O.C.</a><a>Contact</a>
</nav>

<section class="hero" role="img" aria-label="Modern white oceanfront villa with pool at dusk">
  <svg class="hero-arrow l" viewBox="0 0 26 44"><path d="M22 4 4 22l18 18" stroke="#fff" stroke-width="4" fill="none"/></svg>
  <svg class="hero-arrow r" viewBox="0 0 26 44"><path d="M4 4l18 18L4 40" stroke="#fff" stroke-width="4" fill="none"/></svg>
  <div class="hero-box">
    <h1>List with the Leader</h1>
    <div class="hero-btns"><span class="btn btn-blue">Sell Your Home</span><span class="btn btn-dark">Buy Your Home</span></div>
  </div>
</section>

<section class="videos">
  <h2 class="sec-title">List of <span class="hl">Videos</span></h2>
  <p class="sec-sub">Lorem Ipsum is simply dummy text of the printing and typesetting industry</p>
  <div class="video-row">
    <div class="video-card">
      <div class="video-still a" role="img" aria-label="Aerial view of a pool terrace overlooking the ocean">
        <svg width="54" height="54" viewBox="0 0 54 54"><circle cx="27" cy="27" r="26" fill="rgba(0,0,0,.45)" stroke="#fff" stroke-width="2"/><path d="M21 16l16 11-16 11z" fill="#fff"/></svg>
      </div>
      <div class="video-bar"><svg width="10" height="12"><path d="M0 0l10 6-10 6z" fill="#ddd"/></svg><div class="track"><i></i></div><span>01:35 / 04:12</span></div>
    </div>
    <div class="video-card">
      <div class="video-still b" role="img" aria-label="Warm living room interior with fireplace">
        <svg width="54" height="54" viewBox="0 0 54 54"><circle cx="27" cy="27" r="26" fill="rgba(0,0,0,.45)" stroke="#fff" stroke-width="2"/><path d="M21 16l16 11-16 11z" fill="#fff"/></svg>
      </div>
      <div class="video-bar"><svg width="10" height="12"><path d="M0 0l10 6-10 6z" fill="#ddd"/></svg><div class="track"><i></i></div><span>00:48 / 03:20</span></div>
    </div>
  </div>
</section>

<section class="band featured">
  <h2 class="sec-title">Featured Listings</h2>
  <div class="listing-row">
    <div class="listing"><div class="thumb" role="img" aria-label="Aerial view of a hillside estate with lawns" style="background:linear-gradient(160deg,#6f9a5a,#3f6b3c)"></div><h4>Simply Dummy Text</h4><p>Lorem Ipsum is simply dummy text of the printing and typesetting industry.</p><span class="more">Read More »</span></div>
    <div class="listing"><div class="thumb" role="img" aria-label="Courtyard home with arched doorways" style="background:linear-gradient(160deg,#c9a276,#7a5a3b)"></div><h4>Simply Dummy Text</h4><p>Lorem Ipsum is simply dummy text of the printing and typesetting industry.</p><span class="more">Read More »</span></div>
    <div class="listing"><div class="thumb" role="img" aria-label="Bright open-plan living room" style="background:linear-gradient(160deg,#d9d2c4,#8e8272)"></div><h4>Simply Dummy Text</h4><p>Lorem Ipsum is simply dummy text of the printing and typesetting industry.</p><span class="more">Read More »</span></div>
    <div class="listing"><div class="thumb" role="img" aria-label="Dining room with warm lighting" style="background:linear-gradient(160deg,#b27a45,#5c3d22)"></div><h4>Simply Dummy Text</h4><p>Lorem Ipsum is simply dummy text of the printing and typesetting industry.</p><span class="more">Read More »</span></div>
  </div>
</section>

<section class="leader">
  <div class="leader-photo" role="img" aria-label="Portrait of the lead agent"></div>
  <div class="leader-text">
    <h2>List with <span class="hl">the Leader</span></h2>
    <p>Lorem Ipsum is simply dummy text of the printing and typesetting industry. Lorem Ipsum has been the industry's standard dummy text ever since the 1500s, when an unknown printer took a galley of type and scrambled it to make a type specimen book. It has survived not only five centuries, but also the leap into electronic typesetting, remaining essentially unchanged. It was popularised in the 1960s with the release of Letraset sheets containing.</p>
    <span class="btn-read">Read More</span>
  </div>
</section>

<section class="team">
  <h2 class="sec-title">Meet <span class="hl">the Team</span></h2>
  <p class="sec-sub">Lorem Ipsum is simply dummy text of the printing</p>
  <div class="team-row">
    <div class="member m1" role="img" aria-label="Team member portrait"></div>
    <div class="member m2" role="img" aria-label="Team member portrait"><span class="name">Nora Halvey</span></div>
    <div class="member m3" role="img" aria-label="Team member portrait"></div>
    <div class="member m4" role="img" aria-label="Team member portrait"></div>
  </div>
</section>

<section class="band sold">
  <h2 class="sec-title">Previously Sold</h2>
  <div class="sold-row">
    <div class="listing"><div class="thumb" role="img" aria-label="Living room with ocean view" style="background:linear-gradient(160deg,#8fb3cf,#b0804d 60%,#5d3f25)"></div><h4>Simply Dummy Text</h4><p>Lorem Ipsum is simply dummy text of the printing and typesetting industry.</p><span class="more">Read More »</span></div>
    <div class="listing"><div class="thumb" role="img" aria-label="Poolside patio facing the sea" style="background:linear-gradient(180deg,#7fb6dc,#e6e2d6 55%,#3aa0c8)"></div><h4>Simply Dummy Text</h4><p>Lorem Ipsum is simply dummy text of the printing and typesetting industry.</p><span class="more">Read More »</span></div>
    <div class="listing"><div class="thumb" role="img" aria-label="Cliffside home above a beach" style="background:linear-gradient(180deg,#9ccbea,#5f8fae 45%,#c9b48c)"></div><h4>Simply Dummy Text</h4><p>Lorem Ipsum is simply dummy text of the printing and typesetting industry.</p><span class="more">Read More »</span></div>
  </div>
</section>

<footer>
  <div class="site-footer">
    <div class="fcol">
      <h5>About Us</h5>
      <p>Lorem Ipsum has been the industry's standard dummy text ever since the 1500s, when an unknown printer took a galley of type and scrambled it to make a type specimen book. It has survived not only five centuries.</p>
    </div>
    <div class="fcol">
      <h5>Contact Info</h5>
      <p>Address: 1480 Coastline Drive,<br>Laguna Beach, CA 92651</p>
      <p>Phone: 949.555.0142<br>Fax: 949.555.0143</p>
      <p>Email: hello@marwickshore.example</p>
    </div>
    <div class="fcol">
      <h5>Links to Blog</h5>
      <ul>
        <li>Lorem ipsum is simply dummy text</li>
        <li>Lorem ipsum has been the industry's</li>
        <li>Lorem ipsum is simply dummy text</li>
        <li>Lorem ipsum has been the industry's</li>
        <li>Lorem ipsum is simply dummy text</li>
      </ul>
    </div>
  </div>
  <div class="footer-bar">
    <div class="links">Privacy Policy &nbsp;|&nbsp; Terms Conditions &nbsp;|&nbsp; Sitemap &nbsp;|&nbsp; Contact Us</div>
    <div class="copy">Copyright © 2015. All Rights Reserved</div>
    <div class="socials"><i></i><i></i><i></i><i></i><i></i><i></i></div>
    <span class="to-top"></span>
  </div>
</footer>

</body>
</html>
```